We need a complete design for our construction company KELTO CONSTRUCTION based in Auckland New Zealand, we need a logo, website, business card, vehicle design etc..
We are a mid to high-end construction company who work mostly on residential projects and some commercial.

What we want to see in the design;
Professional,
Architectural,
Simple,
Alternative,

We want the design to communicate professionalism, high quality wormanship and and quality service.

Target Market(s)

People looking for a quality building/ construction company

Industry/Entity Type

Construction Company

Contact Information for Business Card

KELTO CONSTRUCTION.co.nz
Lino Verasek
lino@keltoconstruction.example.nz
021 5807 462

Logo Text

KELTO CONSTRUCTION

Number of Pages Required

5+ page

Font styles to use
Sans Serif

Colors

Designer to choose colors to be used in the design.

Requirements
Must have
• Must appear high end, professional, quality, be simple, easy to use, give security to potential clients
Nice to have
• high-quality photos of our recent projects
• about us page
• blog page
• contact us page
• high quality content
Should not have
• should not be hard to use and have too much going on.

```html
<!DOCTYPE html>
<html lang="en">
<head>
<meta charset="utf-8">
<title>Kelto Construction</title>
<link rel="stylesheet" href="https://fonts.googleapis.com/css2?family=Roboto:wght@400;500;700&family=Open+Sans:wght@400;600;700&display=swap">
<style>
:root{
  --yellow:#f6b91a;
  --ink:#2b2b2b;
  --header:#2a2a2a;
  --dark:#3b3b3c;
  --text:#4a4a4a;
  --muted:#666;
  --light:#f3f3f3;
  --white:#fff;
  --line:#bfbfbf;
}
*{box-sizing:border-box;margin:0;padding:0}
html,body{width:1200px;height:2889px;overflow:hidden}
body{position:relative;background:var(--white);font-family:"Open Sans",Arial,sans-serif;color:var(--text)}
.abs{position:absolute}
/* header */
.site-header{position:absolute;left:0;top:0;width:1200px;height:87px;background:var(--header)}
.brand{position:absolute;left:0;top:0;width:341px;height:87px;background:var(--yellow);display:flex;align-items:center;justify-content:center;gap:10px}
.brand-square{width:18px;height:18px;background:var(--ink)}
.brand-name{font-family:"Roboto",Arial,sans-serif;font-weight:700;font-size:19px;color:var(--ink);letter-spacing:.5px}
.main-nav{position:absolute;top:0;height:87px;left:643px;display:flex;align-items:center;gap:0}
.main-nav a{font-family:"Open Sans",Arial,sans-serif;font-size:15px;font-weight:600;color:var(--white);text-decoration:none;margin-right:40px}
.main-nav a.active{color:var(--yellow)}
.search-icon{position:absolute;left:1083px;top:41px}
/* hero */
.hero{position:absolute;left:0;top:87px;width:1200px;height:483px;background:linear-gradient(100deg,#1f5fb8 0%,#2f78d0 45%,#5aa0e6 75%,#3d6fb3 100%)}
.hero-kicker{position:absolute;left:96px;top:198px;font-family:"Roboto",Arial,sans-serif;font-weight:700;font-size:46px;color:var(--yellow);letter-spacing:.5px}
.hero-title{position:absolute;left:96px;top:258px;font-family:"Roboto",Arial,sans-serif;font-weight:400;font-size:40px;line-height:49px;color:var(--white)}
.btn{display:flex;align-items:center;justify-content:center;background:var(--yellow);color:var(--ink);font-family:"Roboto",Arial,sans-serif;font-weight:500;text-decoration:none}
.hero-btn{position:absolute;left:98px;top:383px;width:166px;height:58px;font-size:22px;border:3px solid var(--white)}
.arrow{position:absolute}
/* welcome */
.section-title{position:absolute;left:0;width:1200px;text-align:center;font-family:"Roboto",Arial,sans-serif;font-weight:500;font-size:32px;color:#3a3a3a}
.intro{position:absolute;left:230px;width:740px;top:720px;text-align:center;font-size:13px;line-height:23px;color:var(--text)}
.service-card{position:absolute;top:803px;width:318px}
.service-card .photo{width:318px;height:214px;border:2px solid #ddd}
.service-card h3{margin-top:21px;text-align:center;font-family:"Roboto",Arial,sans-serif;font-weight:500;font-size:18px;color:var(--ink)}
.service-card p{margin-top:10px;text-align:center;font-size:13px;line-height:21px;color:var(--muted);padding:0 30px}
/* about */
.about{position:absolute;left:0;top:1206px;width:1200px;height:466px;background:linear-gradient(180deg,#3d3d3e,#333334)}
.about-video{position:absolute;left:98px;top:1292px;width:503px;height:291px;border:2px solid var(--white);background:linear-gradient(160deg,#8fb3d9 0%,#c9b27f 45%,#5a4a3c 100%)}
.about-title{position:absolute;left:657px;top:1298px;font-family:"Roboto",Arial,sans-serif;font-weight:500;font-size:32px;color:var(--white)}
.about-text{position:absolute;left:657px;top:1356px;width:446px;font-size:13px;line-height:25.5px;color:#e6e6e6;text-align:justify}
.about-btn{position:absolute;left:659px;top:1537px;width:108px;height:39px;font-size:16px;border:2px solid var(--white)}
/* projects */
.project{position:absolute;width:239px;height:171px;border:2px solid #e3e3e3}
/* contact */
.contact-band{position:absolute;left:0;top:2300px;width:1200px;height:443px;background:var(--light)}
.contact-form{position:absolute;left:0;top:2317px;width:663px;height:426px;background:linear-gradient(180deg,#4a463f,#3a3833)}
.form-title{position:absolute;left:98px;top:2360px;font-family:"Roboto",Arial,sans-serif;font-weight:500;font-size:32px;color:var(--white)}
.field{position:absolute;border:2px solid var(--white);color:var(--white);font-size:13px;padding:8px 10px}
.submit{position:absolute;left:98px;top:2658px;width:112px;height:38px;font-size:17px;font-weight:700}
.testimonial-title{position:absolute;left:711px;top:2406px;font-family:"Roboto",Arial,sans-serif;font-weight:500;font-size:32px;color:var(--ink)}
.quote{position:absolute;left:711px;top:2472px;width:390px;font-size:17px;line-height:30px;color:var(--text);text-align:justify}
.qmark{color:var(--yellow);font-family:"Roboto",Arial,sans-serif;font-weight:700;font-size:26px;line-height:0}
.author{position:absolute;left:900px;width:200px;top:2602px;text-align:right;font-family:"Roboto",Arial,sans-serif;font-weight:700;font-size:16px;color:var(--ink)}
.stars{position:absolute;left:1030px;top:2628px}
.dots{position:absolute;left:892px;top:2669px;display:flex;gap:3px}
.dots span{width:7px;height:7px;border-radius:50%;border:1px solid #555}
.dots span.on{background:#333}
/* footer */
.site-footer{position:absolute;left:0;top:2743px;width:1200px;height:146px;background:#2a2a2a}
.footer-nav{position:absolute;top:2792px;left:0;width:1200px;display:flex;justify-content:center;gap:46px}
.footer-nav a{font-size:15px;font-weight:600;color:var(--white);text-decoration:none}
.footer-nav a.active{color:var(--yellow)}
.footer-rule{position:absolute;left:98px;top:2837px;width:1004px;height:1px;background:#666}
.copyright{position:absolute;top:2853px;left:0;width:1200px;text-align:center;font-size:12px;color:#ddd}
</style>
</head>
<body>

<header class="site-header">
  <div class="brand"><span class="brand-square"></span><span class="brand-name">KELTO CONSTRUCTIONS</span></div>
  <nav class="main-nav">
    <a class="active" href="#">Home</a><a href="#">Services</a><a href="#">About</a><a href="#">Projects</a><a href="#">Contact</a>
  </nav>
  <svg class="search-icon" width="16" height="16" viewBox="0 0 16 16"><circle cx="6.5" cy="6.5" r="5" fill="none" stroke="#fff" stroke-width="2"/><line x1="10.2" y1="10.2" x2="15" y2="15" stroke="#fff" stroke-width="2.4"/></svg>
</header>

<section class="hero" role="img" aria-label="Auckland city skyline with high-rise towers under a blue sky"></section>
<svg class="arrow" style="left:34px;top:294px" width="22" height="38" viewBox="0 0 22 38"><polyline points="19,3 4,19 19,35" fill="none" stroke="#fff" stroke-width="4"/></svg>
<svg class="arrow" style="left:1146px;top:294px" width="22" height="38" viewBox="0 0 22 38"><polyline points="3,3 18,19 3,35" fill="none" stroke="#fff" stroke-width="4"/></svg>
<div class="hero-kicker">KELTO CONSTRUCTION</div>
<div class="hero-title">High-end construction company<br>in Auckland, NZ</div>
<a class="btn hero-btn" href="#">Read More</a>

<h2 class="section-title" style="top:662px">Welcome To Kelto Constructions</h2>
<p class="intro">Lorem ipsum dolor sit amet, consectetur adipiscing elit, sed do eiusmod tempor incididunt ut labore et dolore magna aliqua. Ut enim ad minim veniam, quis nostrud exercitation ullamco laboris nisi ut aliquip ex ea commod.</p>

<svg class="arrow" style="left:71px;top:900px" width="12" height="20" viewBox="0 0 12 20"><polyline points="10,2 2,10 10,18" fill="none" stroke="#333" stroke-width="2.5"/></svg>
<svg class="arrow" style="left:1115px;top:900px" width="12" height="20" viewBox="0 0 12 20"><polyline points="2,2 10,10 2,18" fill="none" stroke="#333" stroke-width="2.5"/></svg>

<article class="service-card" style="left:100px">
  <div class="photo" role="img" aria-label="Modern white two-storey residential home on a green hillside" style="background:linear-gradient(180deg,#8a9b7a,#d8d8d2 55%,#5c6b4a)"></div>
  <h3>Residential Construction</h3>
  <p>Lorem Isum is simply dummy text of the printing and typesetting industry.</p>
</article>
<article class="service-card" style="left:439px">
  <div class="photo" role="img" aria-label="Glass office towers seen from below with palm leaves" style="background:linear-gradient(160deg,#2c3a2a 0%,#a9c3e0 35%,#e8f0f8 70%,#7f9bbd 100%)"></div>
  <h3>Commercial Construction</h3>
  <p>Lorem Isum is simply dummy text of the printing and typesetting industry.</p>
</article>
<article class="service-card" style="left:782px">
  <div class="photo" role="img" aria-label="Team reviewing building plans on a table with a hard hat" style="background:linear-gradient(170deg,#b8c9d6 0%,#e9ecef 50%,#c9a65a 100%)"></div>
  <h3>Preconstruction</h3>
  <p>Lorem Isum is simply dummy text of the printing and typesetting industry.</p>
</article>

<section class="about"></section>
<div class="about-video" role="img" aria-label="Video still of workers on a steel tower structure against the sun"></div>
<svg class="abs" style="left:319px;top:1408px" width="62" height="62" viewBox="0 0 62 62"><circle cx="31" cy="31" r="30" fill="#fff"/><polygon points="24,17 46,31 24,45" fill="#f6b91a"/></svg>
<h2 class="about-title">About Us</h2>
<p class="about-text">Lorem ipsum dolor sit amet, consectetur adipiscing elit, sed do eiusmod tempor incididunt ut labore et dolore magna aliqua. Ut enim ad minim veniam, quis nostrud exercitation ullamco laboris nisi ut aliquip ex ea commodo consequat. Duis aute irure dolor in reprehenderit in voluptate velit esse cillum dolore eu fugiat nulla pariatur. Excepteur sint occaecat cupidatat non proident, sunt in culpa qui officia deserunt mollit anim id est laborum.</p>
<a class="btn about-btn" href="#">Read More</a>

<h2 class="section-title" style="top:1768px">Featured Projects</h2>
<div class="project" style="left:100px;top:1849px" role="img" aria-label="Blue two-storey family house with lawn" style="" ></div>
<div class="project" style="left:100px;top:1849px;background:linear-gradient(180deg,#3f7fd0 0%,#2f5a8c 55%,#5e9a3e 100%)" role="img" aria-label="Blue two-storey family house with lawn"></div>
<div class="project" style="left:354px;top:1849px;background:linear-gradient(160deg,#2b6fd6 0%,#1d4a4a 50%,#0f2f33 100%)" role="img" aria-label="Dark glass office tower"></div>
<div class="project" style="left:608px;top:1849px;background:linear-gradient(180deg,#6f8fc4 0%,#d7c8a8 50%,#6b6b66 100%)" role="img" aria-label="Low-rise commercial office building with car park"></div>
<div class="project" style="left:861px;top:1849px;background:linear-gradient(180deg,#3a6fc8 0%,#e6e6e0 45%,#4f7a35 100%)" role="img" aria-label="White heritage villa with garden"></div>
<div class="project" style="left:100px;top:2038px;background:linear-gradient(180deg,#8fb0dc 0%,#8a6b55 50%,#5d7a4a 100%)" role="img" aria-label="Brick and glass office building"></div>
<div class="project" style="left:354px;top:2038px;background:linear-gradient(180deg,#7ec3ea 0%,#dfe3e5 50%,#2fb7d8 100%)" role="img" aria-label="Modern white villa with swimming pool"></div>
<div class="project" style="left:608px;top:2038px;background:linear-gradient(180deg,#2d63c9 0%,#e8ecf2 50%,#3c5f2e 100%)" role="img" aria-label="White and blue striped office block"></div>
<div class="project" style="left:861px;top:2038px;background:linear-gradient(180deg,#4d86d6 0%,#a89b7a 50%,#74a83a 100%)" role="img" aria-label="Large suburban house with green front lawn"></div>

<section class="contact-band"></section>
<div class="contact-form" role="img" aria-label="Dimmed photo of a house exterior behind the contact form"></div>
<h2 class="form-title">Get In Touch</h2>
<div class="field" style="left:98px;top:2423px;width:229px;height:35px">First Name</div>
<div class="field" style="left:362px;top:2423px;width:229px;height:35px">Last Name</div>
<div class="field" style="left:98px;top:2490px;width:229px;height:35px">Phone No</div>
<div class="field" style="left:362px;top:2490px;width:229px;height:35px">Email</div>
<div class="field" style="left:98px;top:2558px;width:493px;height:68px">Message</div>
<a class="btn submit" href="#">Submit</a>

<h2 class="testimonial-title">Words From Our Client</h2>
<p class="quote"><span class="qmark">“</span>&nbsp; Primo stlide feeble ollie north Reno Baskel hel ipop disaster powerslide. Cab flip full-cab method air durometer downhill masonite. Tail slob air poseur death box bearings wall ride. <span class="qmark">”</span></p>
<div class="author">- Jon Mera</div>
<svg class="stars" width="56" height="10" viewBox="0 0 56 10"><g fill="#f6b91a"><polygon points="5,0 6.2,3.6 10,3.6 7,5.9 8.1,9.5 5,7.3 1.9,9.5 3,5.9 0,3.6 3.8,3.6"/><polygon transform="translate(11.5 0)" points="5,0 6.2,3.6 10,3.6 7,5.9 8.1,9.5 5,7.3 1.9,9.5 3,5.9 0,3.6 3.8,3.6"/><polygon transform="translate(23 0)" points="5,0 6.2,3.6 10,3.6 7,5.9 8.1,9.5 5,7.3 1.9,9.5 3,5.9 0,3.6 3.8,3.6"/><polygon transform="translate(34.5 0)" points="5,0 6.2,3.6 10,3.6 7,5.9 8.1,9.5 5,7.3 1.9,9.5 3,5.9 0,3.6 3.8,3.6"/><polygon transform="translate(46 0)" points="5,0 6.2,3.6 10,3.6 7,5.9 8.1,9.5 5,7.3 1.9,9.5 3,5.9 0,3.6 3.8,3.6"/></g></svg>
<div class="dots"><span class="on"></span><span></span><span></span><span></span></div>

<footer class="site-footer"></footer>
<nav class="footer-nav"><a class="active" href="#">Home</a><a href="#">Services</a><a href="#">About</a><a href="#">Projects</a><a href="#">Contact</a></nav>
<div class="footer-rule"></div>
<p class="copyright">Copyrights© 2018 . All Rights Reserved.</p>

</body>
</html>
```